Desktop and Networking Support Course 9.17.25

Important the ad should not be very busy with the text taking up the major part of the ad .. please do not make the text so big that it takes up most of the ad..
Flyer Design Brief for Graphic Artist
also i am looking for something unique or creative that it will stand out .
Size & Layout:
Full Page with Bleed: 8” x 10.75” + 0.25” bleed on all sides.
Footer Space: Leave a 1-inch margin at the bottom for footer content (e.g., contact info, logo, or call-to-action).
Target Audience:
College-age students (around 24 years old)
Located in the USA
Interested in creative, professional, and career-building opportunities
Purpose:
To attract students to enroll in a college program
Flyer should be eye-catching, unique, and creative
Text must be clear and readable,
Design Style:
Use vector art, typography, or photography — your choice
If using photography, feature a white young professional USA citizen:
Wearing a white collared shirt
not with long hair
Creative Direction:
The flyer should stand out visually — something people would want to look at and keep
Showcase creativity and professionalism
Use bold colors, dynamic layout, or unexpected design elements to grab attention
Avoid clutter — keep the design balanced and clean
Text Suggestions (can be adjusted):
Footer,
please leave one inch on the bottom for the footer

```html
<!DOCTYPE html>
<html lang="en">
<head>
<meta charset="utf-8">
<title>Desktop &amp; Networking Course Flyer</title>
<link href="https://fonts.googleapis.com/css2?family=Poppins:wght@400;500;600;700;800&family=Orbitron:wght@800;900&family=Exo+2:wght@300&display=swap" rel="stylesheet">
<style>
  :root {
    --royal: #1f4fc4;
    --gold: #ebb00a;
    --sky-light: #dff1fb;
    --sky: #a9dcf3;
    --ink: #14182a;
    --white: #ffffff;
    --rule: #8aa3b8;
  }
  * { margin: 0; padding: 0; box-sizing: border-box; }
  html, body { width: 962px; height: 1200px; overflow: hidden; background: var(--white); }
  body { font-family: 'Poppins', sans-serif; color: var(--ink); }
  .flyer { position: relative; width: 962px; height: 1200px; overflow: hidden; background: var(--white); }

  .hero {
    position: absolute; left: 0; top: 0; width: 962px; height: 253px;
    background: radial-gradient(ellipse at 50% 40%, #f1f9fe 0%, var(--sky-light) 45%, var(--sky) 100%);
  }
  .headline {
    position: absolute; left: 0; width: 962px; text-align: center;
    top: 26px; font-weight: 800; font-size: 123px; line-height: 1;
    color: var(--royal); letter-spacing: -1px; white-space: nowrap;
  }
  .subline {
    position: absolute; left: 59px; top: 150px; display: flex; align-items: center;
    font-size: 74px; line-height: 1; color: var(--royal); font-weight: 400; white-space: nowrap;
  }
  .cursor-art {
    width: 92px; height: 60px; margin: 0 8px 0 20px; border-radius: 30px;
    background: linear-gradient(135deg, #f7cdb8 0%, #e9b59c 60%, #4a78dc 100%);
  }
  .click-pill {
    background: linear-gradient(180deg, #f2c433, #d99d00); color: var(--white);
    font-weight: 700; font-size: 46px; line-height: 52px; height: 54px;
    padding: 2px 18px 0; border-radius: 28px; margin-right: 12px; letter-spacing: 1px;
  }

  .program-band {
    position: absolute; left: 0; top: 253px; width: 962px; height: 113px;
    background: var(--royal); text-align: center;
  }
  .program-title {
    font-family: 'Orbitron', sans-serif; font-weight: 900; color: var(--gold);
    font-size: 52px; letter-spacing: 1px; margin-top: 8px; line-height: 1.1; white-space: nowrap;
  }
  .program-sub {
    font-family: 'Exo 2', sans-serif; font-weight: 300; color: var(--white);
    font-size: 34px; line-height: 1.2; letter-spacing: 1px;
  }

  .stats-band {
    position: absolute; left: 0; top: 369px; width: 962px; height: 161px; background: var(--gold);
  }
  .stat-big {
    position: absolute; left: 56px; top: 8px; font-weight: 800; color: var(--royal);
    font-size: 118px; line-height: 1; letter-spacing: -4px;
  }
  .stat-big sup { font-size: 66px; vertical-align: top; position: relative; top: 2px; letter-spacing: 0; }
  .stat-label { position: absolute; left: 308px; top: 14px; white-space: nowrap; }
  .stat-label .accent { color: var(--royal); font-weight: 700; font-size: 32px; line-height: 1.2; }
  .stat-label .plain { font-weight: 500; font-size: 31px; line-height: 1.3; }
  .stat-divider { position: absolute; left: 671px; top: 13px; width: 1px; height: 123px; background: #9a7a1a; }
  .rank { position: absolute; left: 706px; top: 10px; }
  .rank .lead { font-weight: 500; font-size: 33px; line-height: 1.1; white-space: nowrap; }
  .rank .num { position: absolute; left: 0; top: 38px; font-weight: 800; color: var(--royal); font-size: 104px; line-height: 1; }
  .rank .tail { position: absolute; left: 67px; top: 40px; font-weight: 600; font-size: 38px; line-height: 1.1; white-space: nowrap; }

  .feature-area {
    position: absolute; left: 0; top: 530px; width: 962px; height: 545px;
    background: radial-gradient(ellipse at 40% 20%, #f4fbff 0%, #cdeaf8 50%, var(--sky) 100%);
  }
  .photo {
    position: absolute; left: 0; top: 477px; width: 530px; height: 598px;
    background: linear-gradient(160deg, #eef5fa 0%, #dde8f0 55%, #c9d6e0 100%);
  }

  .jobs-title {
    position: absolute; left: 548px; top: 560px; width: 356px; text-align: right;
    font-weight: 800; color: var(--royal); font-size: 47px; line-height: 1; white-space: nowrap;
  }
  .rule { position: absolute; left: 545px; width: 360px; height: 1px; background: var(--rule); }
  .ranking-card {
    position: absolute; left: 545px; top: 655px; width: 357px; height: 98px;
    background: var(--white); border-radius: 10px;
    display: flex; align-items: center; justify-content: center; gap: 12px;
  }
  .ranking-card .mark { width: 20px; height: 20px; border-radius: 50%; background: var(--royal); flex: none; }
  .ranking-card .name { font-weight: 700; font-size: 24px; color: var(--royal); white-space: nowrap; }

  .benefit { position: absolute; left: 545px; display: flex; align-items: center; gap: 22px; }
  .benefit .icon { width: 42px; height: 42px; flex: none; }
  .benefit p { font-size: 25px; line-height: 1.12; font-weight: 400; white-space: nowrap; }

  .pill {
    position: absolute; top: 1043px; height: 49px; border-radius: 25px;
    display: flex; align-items: center; gap: 10px; padding-left: 24px;
    font-size: 20px; font-weight: 500; border: 2px solid var(--white); white-space: nowrap;
  }
  .pill svg { width: 22px; height: 22px; flex: none; }
  .pill-format { left: 52px; width: 404px; background: var(--gold); color: var(--ink); }
  .pill-aid { left: 500px; width: 406px; background: var(--royal); color: var(--white); }
</style>
</head>
<body>
<main class="flyer">
  <section class="hero">
    <h1 class="headline">YOUR CAREER</h1>
    <div class="subline">
      <span>Is Just a</span>
      <div class="cursor-art" role="img" aria-label="Illustration of a hand cursor pressing the click button"></div>
      <span class="click-pill">CLICK</span>
      <span>AWAY</span>
    </div>
  </section>

  <section class="program-band">
    <h2 class="program-title">DESKTOP &amp; NETWORKING</h2>
    <p class="program-sub">Master Operating Systems</p>
  </section>

  <section class="stats-band">
    <div class="stat-big">90<sup>%</sup></div>
    <div class="stat-label">
      <div class="accent">EMPLOYMENT RATE</div>
      <div class="plain">Class of 2024</div>
    </div>
    <div class="stat-divider"></div>
    <div class="rank">
      <div class="lead">Prepare for</div>
      <div class="num">3</div>
      <div class="tail">of the<br>Top</div>
    </div>
  </section>

  <section class="feature-area"></section>
  <div class="photo" role="img" aria-label="Photo of a young professional in a white shirt and tie, thinking while working at a desktop computer"></div>

  <h3 class="jobs-title">10 TECH JOBS</h3>
  <div class="rule" style="top:630px"></div>
  <div class="ranking-card">
    <span class="mark"></span>
    <span class="name">National Career Review</span>
  </div>

  <div class="benefit" style="top:791px">
    <svg class="icon" viewBox="0 0 42 42" aria-hidden="true">
      <circle cx="21" cy="21" r="21" fill="var(--royal)"/>
      <circle cx="21" cy="21" r="4" fill="#fff"/>
      <path d="M21 9v8M21 25v8M9 21h8M25 21h8M13 13l5 5M24 24l5 5" stroke="#fff" stroke-width="2"/>
    </svg>
    <p>Hands-On Desktop<br>&amp; Network Training</p>
  </div>
  <div class="rule" style="top:857px"></div>
  <div class="benefit" style="top:877px">
    <svg class="icon" viewBox="0 0 42 42" aria-hidden="true">
      <circle cx="21" cy="21" r="21" fill="var(--royal)"/>
      <circle cx="21" cy="21" r="9" fill="none" stroke="#fff" stroke-width="3" stroke-dasharray="4 3"/>
      <circle cx="21" cy="21" r="4" fill="#fff"/>
    </svg>
    <p>Real-World<br>Troubleshooting Skills</p>
  </div>
  <div class="rule" style="top:945px"></div>
  <div class="benefit" style="top:963px">
    <svg class="icon" viewBox="0 0 42 42" aria-hidden="true">
      <circle cx="21" cy="21" r="21" fill="var(--royal)"/>
      <rect x="12" y="13" width="18" height="12" rx="2" fill="none" stroke="#fff" stroke-width="2.5"/>
      <path d="M16 30h10M21 25v5" stroke="#fff" stroke-width="2.5"/>
    </svg>
    <p>Ready for IT Jobs</p>
  </div>

  <div class="pill pill-format">
    <svg viewBox="0 0 22 22" aria-hidden="true"><circle cx="11" cy="11" r="11" fill="var(--royal)"/><path d="M6 11l3.5 3.5L16 8" stroke="#fff" stroke-width="2.5" fill="none"/></svg>
    In-Person and Remote Options
  </div>
  <div class="pill pill-aid">
    <svg viewBox="0 0 22 22" aria-hidden="true"><circle cx="11" cy="11" r="11" fill="var(--gold)"/><path d="M6 11l3.5 3.5L16 8" stroke="#fff" stroke-width="2.5" fill="none"/></svg>
    Partial Scholarships Offered
  </div>
</main>
</body>
</html>
```